Design a website for a quickly growing ghostwriting and editing firm

DWB Productions has a website through Wix, but we need help! We are based in Austin, TX, and we work primarily with self-help, wellness, and diet authors. We offer ghostwriting, editing and book development services. You can see our basic site now at www.dorawhitbyproductions.com

```html
<!DOCTYPE html>
<html lang="en">
<head>
<meta charset="utf-8">
<title>DWB Productions — Ghostwriting, Editing & Book Development</title>
<link rel="stylesheet" href="https://fonts.googleapis.com/css2?family=Michroma&family=Open+Sans:wght@400;600&display=swap">
<style>
:root{
  --ink:#1f1f1f;
  --body:#8a8a8a;
  --light:#f3f3f3;
  --white:#ffffff;
  --dark:#222222;
  --accent:#e0953a;
  --line:#d9d9d9;
}
*{box-sizing:border-box;margin:0;padding:0}
html,body{width:1200px;height:3624px;overflow:hidden}
body{position:relative;background:var(--white);font-family:"Open Sans",sans-serif;color:var(--ink)}
.abs{position:absolute}
.heading{font-family:"Michroma",sans-serif;font-weight:400;text-transform:uppercase;letter-spacing:1px}
.copy{font-size:15px;line-height:28px;color:var(--body)}
.btn{display:inline-block;border:2px solid var(--ink);border-radius:30px;padding:12px 26px;font-size:14px;font-weight:600;text-transform:uppercase;letter-spacing:.5px;color:var(--ink);text-decoration:none}

/* hero */
.hero{left:0;top:0;width:1200px;height:688px;overflow:hidden;
  background:linear-gradient(90deg,rgba(30,34,20,.75) 0%,rgba(40,40,25,.35) 45%,rgba(0,0,0,0) 70%),
  linear-gradient(160deg,#c9b680 0%,#8f8a4d 35%,#5d7a38 65%,#3d5a26 100%)}
.hero-photo{left:620px;top:0;width:580px;height:688px;background:linear-gradient(180deg,rgba(240,225,200,.25),rgba(90,60,40,.25))}
.brand{left:112px;top:12px;display:flex;align-items:center;gap:12px;color:var(--white);font-family:"Michroma",sans-serif;font-size:22px}
.brand-mark{width:26px;height:26px;border:2px solid var(--white)}
.nav{left:630px;top:38px;display:flex;gap:36px}
.nav a{color:var(--white);font-size:15px;text-decoration:none}
.hero-title{left:112px;top:252px;font-size:54px;color:var(--white);letter-spacing:1px}
.hero-copy{left:112px;top:322px;width:470px;font-size:16px;line-height:28px;color:var(--white)}
.hero .btn{left:112px;top:400px;border-color:var(--white);color:var(--white)}
.dots{left:516px;top:646px;display:flex;gap:14px}
.dots span{width:34px;height:6px;background:rgba(255,255,255,.55)}
.dots span:first-child{background:var(--white)}

/* audiences */
.audience{left:0;top:688px;width:1200px;height:352px;background:var(--light)}
.section-title{width:1200px;left:0;text-align:center;font-size:32px}
.audience .section-title{top:60px}
.aud-col{top:140px;width:300px;text-align:center}
.aud-icon{width:70px;height:70px;margin:0 auto 12px;border-radius:12px;background:#d6d6d6}
.aud-col h3{font-family:"Michroma",sans-serif;font-size:17px;font-weight:400;margin-bottom:10px}
.aud-col p{font-size:14px;line-height:24px;color:var(--body)}

/* services */
.services .section-title{top:1160px}
.svc{top:1232px;height:336px}
.svc-label{top:1594px;width:320px;text-align:center;font-family:"Michroma",sans-serif;font-size:18px}

/* story */
.story{left:0;top:1720px;width:1200px;height:808px;background:var(--light)}
.story .section-title{top:60px}
.story-head{font-family:"Michroma",sans-serif;font-size:32px}
.photo{border-radius:2px}

/* about */
.about-title{left:112px;top:2720px;font-size:48px}
.about-copy{left:112px;top:2792px;width:500px}
.about .btn{left:112px;top:2986px}
.about-frame{left:628px;top:2672px;width:400px;height:472px;border:3px solid var(--accent)}

/* footer */
.footer{left:0;top:3144px;width:1200px;height:480px;background:var(--dark);color:var(--white)}
.f-col{top:76px;font-size:15px;line-height:32px}
.f-col a{display:block;color:var(--white);text-decoration:none}
.divider{top:76px;width:1px;height:200px;background:#555}
.social a{display:flex;align-items:center;gap:10px}
.social i{width:14px;height:14px;border-radius:50%;background:var(--white);display:inline-block}
.subscribe{left:752px;top:64px;width:332px;height:42px;background:var(--white);border-radius:22px;display:flex;align-items:center;padding-left:18px;color:#999;font-size:14px}
.subscribe b{position:absolute;right:3px;top:3px;width:36px;height:36px;border-radius:50%;background:var(--accent)}
.contact{left:760px;top:150px;width:330px;font-size:15px;line-height:30px}
.contact div{display:flex;gap:10px;align-items:flex-start}
.contact svg{flex:none;margin-top:8px}
.f-rule{left:112px;top:390px;width:976px;height:1px;background:#444}
.copyright{left:0;top:430px;width:1200px;text-align:center;font-size:14px;color:#ccc}
</style>
</head>
<body>

<section class="hero abs">
  <div class="hero-photo abs" role="img" aria-label="Young woman with glasses sitting on grass in a sunny park, reading a book"></div>
  <div class="brand abs"><span class="brand-mark"></span>DWB Productions</div>
  <nav class="nav abs"><a href="#">Home</a><a href="#">About</a><a href="#">We Work</a><a href="#">Services</a><a href="#">Blog</a><a href="#">Contact</a></nav>
  <h1 class="hero-title heading abs">DWB Productions</h1>
  <p class="hero-copy abs">We help self-help, wellness and diet authors shape ideas into books readers finish and remember.</p>
  <a class="btn abs" href="#">Get Started</a>
  <div class="dots abs"><span></span><span></span><span></span></div>
</section>

<section class="audience abs">
  <h2 class="section-title heading abs">We Work Primarily With</h2>
  <div class="aud-col abs" style="left:150px">
    <div class="aud-icon" role="img" aria-label="Self-help icon"></div>
    <h3>SELF-HELP</h3>
    <p>Clear, warm books that guide readers through real change, one chapter at a time.</p>
  </div>
  <div class="aud-col abs" style="left:450px">
    <div class="aud-icon" role="img" aria-label="Wellness icon"></div>
    <h3>WELLNESS</h3>
    <p>Grounded writing on health, balance and habits, shaped with experts for everyday readers.</p>
  </div>
  <div class="aud-col abs" style="left:750px">
    <div class="aud-icon" role="img" aria-label="Diet authors icon"></div>
    <h3>DIET AUTHORS</h3>
    <p>Plans, recipes and science turned into friendly pages that keep readers on track.</p>
  </div>
</section>

<section class="services">
  <h2 class="section-title heading abs">Our Services</h2>
  <div class="svc abs" style="left:112px;width:312px;background:linear-gradient(150deg,#3a2614,#7a4a1c 50%,#1a120a)" role="img" aria-label="Candlelit desk with old books and a skull"></div>
  <div class="svc abs" style="left:440px;width:320px;background:linear-gradient(160deg,#cfcfcf,#f1eeea 55%,#d9c7c0)" role="img" aria-label="Printed manuscript being edited with a red pen"></div>
  <div class="svc abs" style="left:776px;width:312px;background:linear-gradient(180deg,#ffffff 10%,#b8473a 35%,#2f5d86 55%,#e0c07a 75%,#ffffff 95%)" role="img" aria-label="Stack of colourful hardcover books"></div>
  <div class="svc-label abs" style="left:108px">GHOSTWRITING</div>
  <div class="svc-label abs" style="left:440px">EDITING</div>
  <div class="svc-label abs" style="left:772px">BOOK DEVELOPMENT</div>
</section>

<section class="story abs">
  <h2 class="section-title heading abs">The Story</h2>
  <h3 class="story-head abs" style="left:112px;top:138px;width:460px;text-align:right">Go on a Journey</h3>
  <p class="copy abs" style="left:112px;top:192px;width:460px;text-align:right">Every book starts with a conversation. We listen to your story, your method and your readers, then map a path from first notes to finished manuscript. Our writers match your voice, our editors sharpen every page, and our team keeps the project moving so you can stay focused on the work you love.</p>
  <div class="photo abs" style="left:596px;top:128px;width:492px;height:312px;background:linear-gradient(200deg,#8e8c86,#5f5b52 50%,#b7b1a6)" role="img" aria-label="Person lying on a wooden pier reading a book"></div>
  <div class="photo abs" style="left:248px;top:472px;width:340px;height:216px;background:linear-gradient(180deg,#5a3c2a 0%,#9a7656 45%,#efe9df 70%,#d8d2c8)" role="img" aria-label="Open book on a table in front of bookshelves"></div>
  <h3 class="story-head abs" style="left:608px;top:480px">Overview of book</h3>
  <p class="copy abs" style="left:608px;top:536px;width:480px">We begin with a clear outline that shows the shape of the whole book, chapter by chapter. From there we draft in stages, share pages for your review and refine until each section reads like you on your best day. When the text is ready we polish structure, flow and detail, then prepare a clean manuscript for your publisher, agent or own launch.</p>
</section>

<section class="about">
  <h2 class="about-title heading abs">About DWB</h2>
  <p class="copy about-copy abs">Based in Austin, Texas, DWB Productions is a growing team of ghostwriters, editors and book developers. We partner with authors in self-help, wellness and diet to turn expertise into books that are easy to read and hard to put down. Whether you have a rough idea or a full draft, we bring the care your book deserves.</p>
  <a class="btn abs" href="#">Read More</a>
  <div class="about-frame abs"></div>
  <div class="photo abs" style="left:660px;top:2640px;width:400px;height:472px;background:linear-gradient(170deg,#f4f1ec,#d9d3c9 55%,#8f9a6f 80%,#e8e2d8)" role="img" aria-label="Woman in a yellow top reading in a lounge chair beside house plants"></div>
</section>

<footer class="footer abs">
  <div class="f-col abs" style="left:112px"><a href="#">Home</a><a href="#">About</a><a href="#">We Work</a><a href="#">Services</a><a href="#">Blog</a><a href="#">Contact</a></div>
  <div class="divider abs" style="left:280px"></div>
  <div class="f-col abs" style="left:336px"><a href="#">Help</a><a href="#">Contact Us</a><a href="#">Terms &amp; Conditions</a><a href="#">Privacy Policy</a></div>
  <div class="divider abs" style="left:512px"></div>
  <div class="f-col social abs" style="left:560px"><a href="#"><i></i>- Newsfeed</a><a href="#"><i></i>- Gallery</a><a href="#"><i></i>- Chirps</a></div>
  <div class="divider abs" style="left:720px"></div>
  <div class="subscribe abs">Email Address<b></b></div>
  <div class="contact abs">
    <div><svg width="14" height="14" viewBox="0 0 24 24"><path fill="#fff" d="M6.6 10.8a15 15 0 0 0 6.6 6.6l2.2-2.2c.3-.3.7-.4 1-.2 1.1.4 2.3.6 3.6.6.6 0 1 .4 1 1V20c0 .6-.4 1-1 1A17 17 0 0 1 3 4c0-.6.4-1 1-1h3.5c.6 0 1 .4 1 1 0 1.3.2 2.5.6 3.6.1.3 0 .7-.2 1z"/></svg><span>Phone - 512-555-0148</span></div>
    <div><svg width="14" height="14" viewBox="0 0 24 24"><path fill="#fff" d="M2 5h20v14H2zm2 2v.5l8 5 8-5V7z"/></svg><span>Email - hello@dwbproductions.com</span></div>
    <div><svg width="14" height="14" viewBox="0 0 24 24"><path fill="#fff" d="M12 2a7 7 0 0 0-7 7c0 5 7 13 7 13s7-8 7-13a7 7 0 0 0-7-7zm0 9.5A2.5 2.5 0 1 1 12 6.5a2.5 2.5 0 0 1 0 5z"/></svg><span>Address - 418 Juniper Lane, Austin, TX 78701</span></div>
  </div>
  <div class="f-rule abs"></div>
  <div class="copyright abs">© 2021 All Rights Reserved</div>
</footer>

</body>
</html>
```